Flyer, poster, banner and social media titles designs for Community Mending Chartre

The Harbourline Charter for Community Mending provide a nationally agreed framework to guide recovery policy and practice across Australia. The Principles support recovery practitioners, governments, non-government organisations and communities to deliver effective, community-centred recovery outcomes.
The Principles have recently been refreshed through extensive consultation and we require a contemporary visual identity and design suite that will increase awareness, engagement and practical application of the Principles.
The redesign will cover:
• A4 Brochure (primary publication)
• A3 Poster
• Pull up banner
• Social Media Tiles
The new design should:
• Create a recognisable brand for the Harbourline Charter.
• Appeal to both experienced and emerging recovery practitioners.
• Reflect contemporary disaster recovery practice.
• Feel people-focused rather than government-focused.
• Support future resources such as videos, implementation guides, presentations and workshop materials.
• Remain relevant for several years without requiring a major redesign.
Target Audience
• Disaster recovery practitioners
• Government agencies
• Non-government organisations
• Community recovery workers
• Recovery managers and leaders
• Community stakeholders and volunteers
The visual identity should reflect the six Principles:
• Understanding Context
• Recognising Complexity
• Community-Centred Approaches
• Coordination
• Communication
• Capacity Building
The design should communicate:
• Recovery is centred on people and communities.
• Recovery is collaborative and involves many sectors.
• Recovery is adaptive, inclusive and evidence-informed.
• Recovery supports resilience and long-term wellbeing.
• The Principles provide practical guidance for recovery practice.
We are looking for:
• Modern and professional
• Warm and approachable
• Human-centred
• Inclusive and accessible
• Australian in context
• Visually engaging
• Suitable for print and digital use
We would like to avoid:
• Images of disaster destruction
• Emergency response imagery (fire trucks, flashing lights, etc.)
• Overly corporate or bureaucratic designs
• Designs that focus on deficits rather than recovery and growth
Consider themes such as:
• Connection and collaboration
• Communities and people
• Growth, recovery and renewal
Accessibility
Designs should:
• Meet accessibility best practice
• Use clear typography
• Achieve strong colour contrast
• Be suitable for both digital and print formats

Deliverables
1. Principles Brochure
• A4 trifold size x 2 (online and print friendly version)
• A side to include cover side, logos side and overview of principles.
• B side full details of the principles
• Graphic to highlight the 3 c’s concept (RECOVERY Context, complexity, community centred, coordinate, communicate and capacity). Currently 3 circles.
• Can be printed and distributed electronically
2. Poster
• A1 and A3 versions
• Suitable for office and workshop display
3. Pull-Up Banner - 850 mm (W) × 2000 mm (H)
• Conference and event use
• High visual impact
• Strong branding and concise messaging
4. Social Media Tiles x 3

We are providing an extension and increasing the budget following feedback from designers. We are wanting the resources to look and feel different from the existing designs, considering either a different colour palette in the designs or different motif with the leave design. Any nature based designs should consider the Australian fauna or flora. Also suggest avoiding images in the designs. The principles are not numbered or liner in the concept of how they function. Happy to answer any further questions and thank you for your suggested concepts.

Disaster recovery practitioners, Government agencies , Non-government organisations, Community recovery workers and Community stakeholders and volunteers

Disaster recovery

• Modern, warm, visually engaging, human-centred, Australian in context and different to the current design.
• Symbols for each principles
• Images of disaster destruction, Emergency response imagery, Overly corporate or bureaucratic designs, Designs that focus on deficits rather than recovery and growth, avoid too much black

```html
<!DOCTYPE html>
<html lang="en">
<head>
<meta charset="utf-8">
<title>Harbourline Charter for Community Mending – Trifold</title>
<link href="https://fonts.googleapis.com/css2?family=Open+Sans:wght@300;400;600;700&display=swap" rel="stylesheet">
<style>
:root{
  --page:#ece8e1;
  --teal:#2c6b66;
  --teal-mid:#3b7f78;
  --teal-deep:#1f4e4a;
  --wattle:#e2a72e;
  --ochre:#c9632f;
  --sand:#f6e9cc;
  --sand-soft:#fbf6ec;
  --ink:#263533;
  --white:#ffffff;
  --line:#e6dfd2;
  --mark:#d8cfbf;
}
*{margin:0;padding:0;box-sizing:border-box}
html,body{width:1200px;height:498px;overflow:hidden}
body{background:var(--page);font-family:"Open Sans",sans-serif;color:var(--ink);position:relative}

/* inside spread */
.spread-inside{position:absolute;left:36px;top:36px;width:549px;height:425px;display:grid;grid-template-columns:repeat(3,183px);grid-template-rows:36px 195px 37px 157px;box-shadow:0 1px 3px rgba(0,0,0,.15)}
.principle-head{display:flex;align-items:center;gap:8px;padding-left:22px;background:var(--sand);color:var(--teal-deep)}
.principle-head.dark{background:var(--teal-deep);color:var(--white)}
.principle-head .icon{width:22px;height:22px;border-radius:50%;background:var(--ochre);flex:none;display:flex;align-items:center;justify-content:center}
.principle-head.dark .icon{background:var(--wattle)}
.principle-head .pre,.principle-head .post{font-size:5.6px;line-height:1.2;display:block}
.principle-head .name{font-size:12px;font-weight:600;letter-spacing:.3px;line-height:1.1;display:block}
.principle-body{background:var(--teal);color:var(--white);font-size:5.3px;line-height:7.6px;padding:8px 12px 0 14px;overflow:hidden}
.principle-body.white{background:var(--sand-soft);color:var(--ink)}
.principle-body p{margin:0}

/* outside spread */
.spread-outside{position:absolute;left:617px;top:38px;width:549px;height:425px;display:grid;grid-template-columns:183px 183px 183px;box-shadow:0 1px 3px rgba(0,0,0,.15)}
.panel{position:relative;overflow:hidden;background:var(--white)}
.overview{padding:11px 12px 0 15px;background:var(--sand-soft)}
.overview .kicker{font-size:5.6px;letter-spacing:.2px;color:var(--ink)}
.overview .title{font-size:19px;font-weight:300;line-height:20px;margin-top:2px;color:var(--teal-deep)}
.overview .title .accent{color:var(--ochre);display:block}
.overview .intro{font-size:4.9px;line-height:7.6px;margin-top:8px}
.overview h2{font-size:8.4px;font-weight:600;color:var(--teal);line-height:11px;margin-top:10px;letter-spacing:.2px}
.overview .relation{font-size:5.7px;line-height:9.7px;margin-top:6px}
.diagram{position:absolute;left:11px;top:261px;width:162px;height:162px}

.partners{border-left:1px solid var(--line);border-right:1px solid var(--line)}
.partners h2{height:25px;text-align:center;font-size:13px;font-weight:700;line-height:25px;color:var(--teal-deep);border-bottom:1px solid var(--line)}
.partners h2 span{color:var(--ochre)}
.partner-grid{display:grid;grid-template-columns:1fr 1fr;grid-template-rows:59px 73px 78px 79px 53px}
.partner{display:flex;flex-direction:column;align-items:center;justify-content:center;gap:4px;border-bottom:1px solid var(--line);padding:0 6px;text-align:center;font-size:5.6px;font-weight:600;line-height:7px;color:var(--ink)}
.partner:nth-child(odd){border-right:1px solid var(--line)}
.partner .mark{width:18px;height:18px;border-radius:50%;background:var(--mark)}
.dev-title{text-align:center;font-size:6px;font-weight:600;letter-spacing:.3px;margin-top:12px;color:var(--teal-deep)}
.dev-row{display:flex;justify-content:space-around;margin-top:10px;padding:0 4px}
.dev{display:flex;align-items:center;gap:4px;font-size:5px;font-weight:600;line-height:6px;max-width:80px}
.dev .mark{width:12px;height:12px;background:var(--mark);flex:none}

.cover{background:var(--sand-soft)}
.cover-band{position:absolute;inset:0}
.cover-text{position:absolute;left:0;top:0;width:100%;padding:22px 0 0 23px;color:var(--white)}
.cover-text .kicker{font-size:5.6px;letter-spacing:.2px}
.cover-text .title{font-size:17px;font-weight:300;line-height:18px;margin-top:2px}
.cover-text .title span{color:var(--wattle)}
.tagline{position:absolute;left:0;width:100%;top:88px;text-align:center;color:var(--white);font-size:13px;font-weight:700;line-height:17.5px}
.tagline-rule{position:absolute;left:72px;top:147px;width:39px;height:1.5px;background:var(--wattle)}
.flower-art{position:absolute;left:18px;top:196px;width:160px;height:225px;border-radius:60px 20px 0 0;background:radial-gradient(ellipse at 45% 50%,#b8741f 0%,#e2a72e 35%,rgba(201,99,47,.45) 62%,rgba(251,246,236,0) 85%)}
</style>
</head>
<body>

<section class="spread-inside" aria-label="Principles in detail">
  <header class="principle-head"><span class="icon"><svg width="11" height="11" viewBox="0 0 12 12"><rect x="2" y="1" width="8" height="6" fill="#fff"/><rect x="1" y="8" width="3" height="3" fill="#fff"/><rect x="5" y="8" width="3" height="3" fill="#fff"/><rect x="9" y="8" width="2" height="3" fill="#fff"/></svg></span><div><span class="pre">Understand the</span><span class="name">CONTEXT</span></div></header>
  <header class="principle-head dark"><span class="icon"><svg width="11" height="11" viewBox="0 0 12 12"><circle cx="6" cy="3" r="2" fill="#fff"/><circle cx="2.5" cy="7" r="1.5" fill="#fff"/><circle cx="9.5" cy="7" r="1.5" fill="#fff"/><rect x="4" y="6" width="4" height="5" rx="1" fill="#fff"/></svg></span><div><span class="name">COORDINATE</span><span class="post">all activities</span></div></header>
  <header class="principle-head"><span class="icon"><svg width="11" height="11" viewBox="0 0 12 12"><circle cx="6" cy="6" r="3" fill="none" stroke="#fff" stroke-width="1.5"/><circle cx="6" cy="6" r="1" fill="#fff"/></svg></span><div><span class="pre">Recognise and build</span><span class="name">CAPACITY</span></div></header>

  <div class="principle-body"><p>• Successful recovery recognises, supports and builds on individual, community and organisational capacity and resilience. Recovery should:<br>• Assess capability and capacity requirements before, during and after a disaster;<br>• Support the development of self-reliance, preparation and disaster mitigation;<br>• Quickly identify and mobilise community skills, strengths and resources;<br>• Develop networks and partnerships to strengthen capacity, capability and resilience;<br>• Provide opportunities to share, transfer and develop knowledge, skills and training;<br>• Recognise that resources can be provided by a range of partners and from community networks;<br>• Acknowledge that existing resources may be stretched, and that additional resources may be sought;<br>• Understand that additional resources may only be available for a limited period, and that sustainability may need to be addressed;<br>• Understand when and how to step back, while continuing to support individuals and the community as a whole to be more<br>• Be evaluated to provide learning for future and improved resilience</p></div>
  <div class="principle-body white"><p>Successful recovery requires a planned, coordinated and adaptive approach, between community and partner agencies, based on continuing assessment of impacts and need. Recovery should:<br>• Have clearly articulated and shared goals based on desired outcomes;<br>• Be flexible, taking into account changes in community needs or stakeholder expectations;<br>• Be guided by those with experience and expertise, using skilled, authentic and capable community leadership;<br>• Be at the pace desired by the community, and seek to collaborate and reconcile different interests and time frames;<br>• Reflect well-developed community planning and information gathering before, during and after a disaster;<br>• Have clear decision-making and reporting structures and sound governance, which are transparent and accessible to the community;<br>• Demonstrate an understanding of the roles, responsibilities and authority of organisations involved and coordinate across agencies to ensure minimal service provision disruption;<br>• Be part of an emergency management approach that integrates with response operations and contributes to future prevention and preparedness; and</p></div>
  <div class="principle-body"><p>• Successful recovery recognises, supports and builds on individual, community and organisational capacity and resilience. Recovery should:<br>• Assess capability and capacity requirements before, during and after a disaster;<br>• Support the development of self-reliance, preparation and disaster mitigation;<br>• Quickly identify and mobilise community skills, strengths and resources;<br>• Develop networks and partnerships to strengthen capacity, capability and resilience;<br>• Provide opportunities to share, transfer and develop knowledge, skills and training;<br>• Recognise that resources can be provided by a range of partners and from community networks;<br>• Acknowledge that existing resources may be stretched, and that additional resources may be sought;<br>• Understand that additional resources may only be available for a limited period, and that sustainability may need to be addressed;<br>• Understand when and how to step back, while continuing to support individuals and the community as a whole to be more<br>• Be evaluated to provide learning for future and improved resilience</p></div>

  <header class="principle-head"><span class="icon"><svg width="11" height="11" viewBox="0 0 12 12"><rect x="1" y="2" width="10" height="6" rx="2" fill="#fff"/><path d="M3 8 L3 11 L6 8Z" fill="#fff"/></svg></span><div><span class="pre">Recognise</span><span class="name">COMMUNICATE</span></div></header>
  <header class="principle-head dark"><span class="icon"><svg width="11" height="11" viewBox="0 0 12 12"><circle cx="3" cy="4" r="1.5" fill="#fff"/><circle cx="6" cy="3" r="1.5" fill="#fff"/><circle cx="9" cy="4" r="1.5" fill="#fff"/><path d="M1 11 Q6 5 11 11Z" fill="#fff"/></svg></span><div><span class="pre">Use</span><span class="name">COMMUNITY-LED</span><span class="post">approaches</span></div></header>
  <header class="principle-head"><span class="icon"><svg width="11" height="11" viewBox="0 0 12 12"><circle cx="4" cy="4" r="2" fill="#fff"/><path d="M1 11 Q4 6 7 11Z" fill="#fff"/><rect x="7" y="1" width="4" height="3" rx="1" fill="#fff"/></svg></span><div><span class="name">COMMUNICATE</span><span class="post">Effectively</span></div></header>

  <div class="principle-body"><p style="line-height:8.3px">Successful recovery is responsive to the complex and dynamic nature of both emergencies and the community. Recovery should recognise that:<br>• Disasters lead to a range of effects and impacts that require a variety of approaches; they can also leave long-term legacies;<br>• Information impacts is limited at first &amp; changes over time;<br>• Affected individuals and the community have diverse needs, wants and expectations, which can evolve rapidly;<br>• Responsive and flexible action is crucial to address immediate needs;<br>• Existing community knowledge and values may challenge the assumptions of those outside of the community;<br>• Conflicting knowledge, values and priorities among individuals, the community and organisations may create tensions;</p></div>
  <div class="principle-body white"><p>• Successful recovery recognises, supports and builds on individual, community and organisational capacity and resilience. Recovery should:<br>• Assess capability and capacity requirements before, during and after a disaster;<br>• Support the development of self-reliance, preparation and disaster mitigation;<br>• Quickly identify and mobilise community skills, strengths and resources;<br>• Develop networks and partnerships to strengthen capacity, capability and resilience;<br>• Provide opportunities to share, transfer and develop knowledge, skills and training;<br>• Recognise that resources can be provided by a range of partners and from community networks;<br>• Acknowledge that existing resources may be stretched, and that additional resources may be sought;<br>• Understand that additional resources may only be available for a limited period, and that sustainability may need to be addressed;</p></div>
  <div class="principle-body"><p style="line-height:8.3px">Successful recovery is built on effective communication between the affected community and other partners. Recovery should:<br>• Recognise that communication should be two-way, and that input and feedback should be encouraged;<br>• Ensure that information is accessible to audiences in diverse situations, addresses a variety of communication needs, and is provided through a range of media and networks;<br>• Establish mechanisms for coordinated and consistent communications between all service providers, organisations and individuals and the community;<br>• Ensure that all communication is relevant, timely, clear, accurate, targeted, credible and consistent; and<br>• Identify trusted sources of information and repeat key recovery messages to enable greater community confidence and receptivity.</p></div>
</section>

<section class="spread-outside" aria-label="Cover, partners and overview">
  <article class="panel overview">
    <p class="kicker">HARBOURLINE CHARTER FOR</p>
    <h1 class="title">Community<span class="accent">Mending</span></h1>
    <p class="intro">Disasters can deeply impact lives and livelihoods. Working with communities recovering from disasters is complex and challenging. These principles are a way to guide our efforts, our approach, our planning and our decision-making. Disaster recovery is part of emergency management, which includes the broader components of prevention, preparedness and response. Planning for recovery is integral to emergency preparation and mitigation actions may often be initiated as part of recovery. Disaster recovery includes built, environmental and economic elements, all contributing to individual and social wellbeing. Recovery can provide an opportunity to improve these aspects beyond previous conditions, contributing to a more resilient community.</p>
    <h2>THE RELATIONSHIP BETWEEN<br>THE PRINCIPLES</h2>
    <p class="relation">While all the principles are equally critical to ensure effective recovery, understanding the local and broader context and recognising complexity are foundational. The descriptions beneath each principle overleaf provide further guidance for working with communities in disaster recovery. ISBN 978-0-64512-830-4 (pdf/online)</p>
    <svg class="diagram" viewBox="0 0 162 162" role="img" aria-label="Principles wheel around successful recovery">
      <defs>
        <path id="ring-outer" d="M16 81 a65 65 0 1 1 130 0 a65 65 0 1 1 -130 0"/>
        <path id="ring-inner" d="M33 81 a48 48 0 1 1 96 0 a48 48 0 1 1 -96 0"/>
      </defs>
      <path d="M81 81 L81 3 A78 78 0 0 0 3 81Z" fill="#2c6b66"/>
      <path d="M81 81 L159 81 A78 78 0 0 0 81 3Z" fill="#3b7f78"/>
      <path d="M81 81 L81 159 A78 78 0 0 0 159 81Z" fill="#2c6b66"/>
      <path d="M81 81 L3 81 A78 78 0 0 0 81 159Z" fill="#3b7f78"/>
      <path d="M25 81 A56 56 0 0 1 137 81Z" fill="#c9632f"/>
      <path d="M25 81 A56 56 0 0 0 137 81Z" fill="#b5822a"/>
      <circle cx="81" cy="81" r="37" fill="#fbf6ec"/>
      <g font-family="Open Sans, sans-serif" font-weight="600" fill="#fff" font-size="8" letter-spacing="0.8">
        <text><textPath href="#ring-outer" startOffset="12%" text-anchor="middle">COMMUNICATE</textPath></text>
        <text><textPath href="#ring-outer" startOffset="41%" text-anchor="middle">COMMUNITY-LED</textPath></text>
        <text><textPath href="#ring-outer" startOffset="62%" text-anchor="middle">CAPACITY</textPath></text>
        <text><textPath href="#ring-outer" startOffset="88%" text-anchor="middle">COORDINATE</textPath></text>
        <text font-size="7.5"><textPath href="#ring-inner" startOffset="25%" text-anchor="middle">CONTEXT</textPath></text>
        <text font-size="7.5"><textPath href="#ring-inner" startOffset="75%" text-anchor="middle">COMPLEXITY</textPath></text>
      </g>
      <text x="81" y="79" text-anchor="middle" font-family="Open Sans, sans-serif" font-weight="600" font-size="7" fill="#2c6b66">SUCCESSFUL</text>
      <text x="81" y="89" text-anchor="middle" font-family="Open Sans, sans-serif" font-weight="600" font-size="7" fill="#263533">RECOVERY</text>
    </svg>
  </article>

  <article class="panel partners">
    <h2>Our <span>Partners</span></h2>
    <div class="partner-grid">
      <div class="partner"><span class="mark"></span>Federal Human Services Office</div>
      <div class="partner"><span class="mark"></span>Federal Home Affairs Office</div>
      <div class="partner"><span class="mark"></span>Southern Aid Society</div>
      <div class="partner"><span class="mark"></span>Southgate State Government</div>
      <div class="partner"><span class="mark"></span>Westreach State Government</div>
      <div class="partner"><span class="mark"></span>Islandmere Government</div>
      <div class="partner"><span class="mark"></span>Northcoast Government</div>
      <div class="partner"><span class="mark"></span>Capital Region Government</div>
      <div class="partner"><span class="mark"></span>Topend Territory Government</div>
      <div class="partner"><span class="mark"></span>Eastvale State Government</div>
    </div>
    <p class="dev-title">PARTNERS IN DEVELOPMENT FROM THE</p>
    <div class="dev-row">
      <div class="dev"><span class="mark"></span>Coastal Office of Emergency Planning</div>
      <div class="dev"><span class="mark"></span>Social Mending Reference Group</div>
    </div>
  </article>

  <article class="panel cover">
    <svg class="cover-band" viewBox="0 0 183 425" preserveAspectRatio="none" aria-hidden="true"><path d="M0 0 H183 V187 Q120 160 60 176 Q25 186 0 195Z" fill="#2c6b66"/></svg>
    <div class="cover-text">
      <p class="kicker">HARBOURLINE CHARTER FOR</p>
      <p class="title">Community<br><span>Mending</span></p>
    </div>
    <p class="tagline">Working together to<br>Strengthen Community<br>Recovery</p>
    <span class="tagline-rule"></span>
    <div class="flower-art" role="img" aria-label="Botanical illustration of a native wattle bloom in gold and ochre"></div>
  </article>
</section>

</body>
</html>
```